Harborline Renewal Business Card Design

Professional and clean design. The design colors should flow with the logo. Two-sided card with the website on the back which is:

www.HarborlineRenewal.example.

"Specializing in Water Damage Restoration"

On the front I need the name, email, phone, and logo.

Name: Darnell Quisby
Email: Darnell@HarborlineRenewal.example
Phone: 555-318-2046 for now

I only have the Preview and Thumbnail right now but should have the source files uploaded within a day or two.

Target Market(s)

Flood victims, home owners with water damage from busted pipes etc...

Industry/Entity Type

Business

Contact Information for Business Card

Name: Darnell Quisby

Font styles to use
Serif
Sans Serif

Requirements
Must have
• Business Card Details Info

```html
<!DOCTYPE html>
<html lang="en">
<head>
<meta charset="utf-8">
<title>Harborline Renewal Business Card</title>
<link href="https://fonts.googleapis.com/css2?family=Cinzel:wght@400&family=Open+Sans:wght@400;600&display=swap" rel="stylesheet">
<style>
  :root {
    --page-bg: #e9ecef;
    --card-top: #52c1ef;
    --card-bottom: #2893d5;
    --ink-white: #ffffff;
    --mark-blue: #2a95d6;
  }
  * { box-sizing: border-box; margin: 0; padding: 0; }
  html, body { width: 1200px; height: 900px; overflow: hidden; }
  body {
    position: relative;
    background: var(--page-bg);
    font-family: "Open Sans", Arial, sans-serif;
    color: var(--ink-white);
  }
  .card {
    position: absolute;
    overflow: hidden;
    background: linear-gradient(180deg, var(--card-top) 0%, var(--card-bottom) 100%);
    box-shadow: 0 6px 18px rgba(0,0,0,0.18);
  }

  /* Company name lockup: large word over a ruled small-caps line */
  .brand-name {
    font-family: "Cinzel", "Times New Roman", serif;
    font-weight: 400;
    color: var(--ink-white);
    white-space: nowrap;
    display: inline-flex;
    flex-direction: column;
    align-items: stretch;
    text-align: center;
  }
  .brand-word { display: block; line-height: 1; letter-spacing: 1px; }
  .brand-sub {
    display: flex;
    align-items: center;
    gap: 8px;
    line-height: 1;
    letter-spacing: 4px;
  }
  .brand-sub::before,
  .brand-sub::after {
    content: "";
    flex: 1;
    height: 2px;
    background: var(--ink-white);
  }

  /* Front side */
  .card-front { left: 78px; top: 35px; width: 587px; height: 362px; }
  .card-front .corner-circle {
    position: absolute;
    left: -120px; top: -40px;
    width: 400px; height: 400px;
    border-radius: 50%;
    background: var(--ink-white);
    border: 10px solid var(--mark-blue);
    box-shadow: 0 0 0 6px var(--ink-white);
  }
  .card-front .brand-name {
    position: absolute;
    right: 38px; top: 52px;
  }
  .card-front .brand-word { font-size: 37px; }
  .card-front .brand-sub { font-size: 16px; margin-top: 6px; }
  .card-front .holder-name {
    position: absolute;
    right: 36px; top: 232px;
    font-size: 21px;
    font-weight: 600;
  }
  .contact-list {
    position: absolute;
    right: 36px; top: 281px;
    list-style: none;
    text-align: right;
    font-size: 14.5px;
    line-height: 28px;
  }
  .contact-list li { display: flex; justify-content: flex-end; align-items: center; gap: 8px; }
  .contact-list svg { width: 12px; height: 12px; fill: var(--ink-white); }

  /* Back side */
  .card-back { left: 388px; top: 505px; width: 567px; height: 352px; text-align: center; }
  .card-back .brand-lockup {
    position: absolute;
    left: 0; right: 0; top: 132px;
    display: flex; justify-content: center; align-items: center; gap: 14px;
  }
  .card-back .brand-dot {
    width: 86px; height: 86px;
    border-radius: 50%;
    background: var(--ink-white);
    flex: none;
  }
  .card-back .brand-word { font-size: 39px; }
  .card-back .brand-sub { font-size: 17px; margin-top: 6px; }
  .card-back .website {
    position: absolute; left: 0; right: 0; top: 248px;
    font-size: 15px; font-weight: 600;
  }
  .card-back .tagline {
    position: absolute; left: 0; right: 0; top: 291px;
    font-size: 17.5px; font-weight: 600;
  }
</style>
</head>
<body>
  <section class="card card-front" aria-label="Business card front">
    <div class="corner-circle"></div>
    <h1 class="brand-name">
      <span class="brand-word">HARBORLINE</span>
      <span class="brand-sub">RENEWAL</span>
    </h1>
    <p class="holder-name">Darnell Quisby</p>
    <ul class="contact-list">
      <li>555-318-2046
        <svg viewBox="0 0 24 24" aria-hidden="true"><path d="M6.6 10.8a15.1 15.1 0 0 0 6.6 6.6l2.2-2.2a1 1 0 0 1 1-.25 11.4 11.4 0 0 0 3.6.57 1 1 0 0 1 1 1V20a1 1 0 0 1-1 1A17 17 0 0 1 3 4a1 1 0 0 1 1-1h3.5a1 1 0 0 1 1 1c0 1.25.2 2.45.57 3.57a1 1 0 0 1-.25 1z"/></svg>
      </li>
      <li>Darnell@HarborlineRenewal.example
        <svg viewBox="0 0 24 24" aria-hidden="true"><path d="M2 5h20v14H2z" fill="#fff"/><path d="M3 6l9 7 9-7" fill="none" stroke="#2a95d6" stroke-width="1.6"/></svg>
      </li>
    </ul>
  </section>

  <section class="card card-back" aria-label="Business card back">
    <div class="brand-lockup">
      <span class="brand-dot"></span>
      <h2 class="brand-name">
        <span class="brand-word">HARBORLINE</span>
        <span class="brand-sub">RENEWAL</span>
      </h2>
    </div>
    <p class="website">www.HarborlineRenewal.example</p>
    <p class="tagline">Specializing in Water Damage Restoration</p>
  </section>
</body>
</html>
```